Need help in designing new business card utilizing our new logo.

BuildMark Solutions works with Construction Business Owners, Managers & IT Professionals to strengthen software usage and increase user productivity.

Our Construction Accounting and Mobile Field Management Software Clients engage with us in the following areas:

New Software Implementations
Software Re-Implementations
Redesigning Software Usage at the User Level
Project Coordination & Management
Continued Software Support

Old tag line:
Mapping Choices - Building Better Systems

www.buildmark-solutions.example

Ridge 4 is a product, but not needed for a new business card.

```html
<!DOCTYPE html>
<html lang="en">
<head>
<meta charset="utf-8">
<title>BuildMark Solutions – Business Card</title>
<link rel="stylesheet" href="https://fonts.googleapis.com/css2?family=Roboto:wght@400;500;700&family=Roboto+Condensed:wght@700&display=swap">
<style>
  :root {
    --brand-blue: #0d1a9c;
    --brand-grey: #a9aaad;
    --ink: #3a3a3c;
    --card: #f1f1f2;
    --backdrop: #b4b4b4;
    --white: #ffffff;
  }
  * { box-sizing: border-box; margin: 0; padding: 0; }
  html, body { width: 1200px; height: 576px; overflow: hidden; }
  body {
    background: var(--backdrop);
    font-family: "Roboto", Arial, sans-serif;
    position: relative;
  }
  .card {
    position: absolute;
    top: 139px;
    width: 484px;
    height: 294px;
    background: var(--card);
    border-radius: 14px;
    overflow: hidden;
    box-shadow: 0 3px 6px rgba(0,0,0,0.25);
  }
  .card--front { left: 82px; }
  .card--back { left: 602px; }

  /* Front */
  .front-brand {
    position: absolute;
    top: 64px; left: 0; right: 0;
    display: flex; align-items: center; justify-content: center; gap: 12px;
  }
  .brand-square { width: 30px; height: 30px; background: var(--brand-blue); }
  .brand-name {
    color: var(--brand-blue);
    font-weight: 700;
    font-size: 30px;
    letter-spacing: 0.5px;
    line-height: 1;
  }
  .services-band {
    position: absolute;
    top: 167px; left: 0; right: 0; height: 80px;
    background: var(--brand-blue);
    color: var(--white);
    font-size: 13px;
    line-height: 18.5px;
    text-align: center;
    display: flex; flex-direction: column; justify-content: center;
  }
  .services-band .sep { margin: 0 8px; }
  .front-web {
    position: absolute;
    top: 262px; left: 0; right: 0;
    display: flex; align-items: center; justify-content: center; gap: 14px;
    color: var(--brand-blue);
    font-size: 12px;
  }
  .front-web .rule { width: 40px; height: 1px; background: var(--brand-grey); }

  /* Back */
  .back-brand {
    position: absolute; top: 34px; left: 20px;
    color: var(--brand-blue);
    font-weight: 700;
    font-size: 30px;
    line-height: 1;
  }
  .name-marker {
    position: absolute; top: 110px; left: -14px;
    width: 28px; height: 28px; border-radius: 50%;
    background: var(--brand-blue);
  }
  .person-name {
    position: absolute; top: 110px; left: 20px;
    font-family: "Roboto Condensed", Arial, sans-serif;
    font-weight: 700; font-size: 20px;
    color: var(--brand-blue);
  }
  .person-role {
    position: absolute; top: 136px; left: 20px;
    font-size: 12px; color: var(--ink);
  }
  .contact-list {
    position: absolute; top: 165px; left: 20px;
    list-style: none;
    font-size: 12px; color: var(--ink);
  }
  .contact-list li {
    display: flex; align-items: center; gap: 10px;
    height: 17.6px;
  }
  .contact-list svg { width: 11px; height: 11px; fill: var(--brand-blue); flex: none; }
  .contact-list .web-accent { color: var(--brand-blue); }
  .address {
    position: absolute; top: 238px; left: 20px;
    font-size: 12px; line-height: 16.5px; color: var(--ink);
    font-style: normal;
  }
  .tagline-band {
    position: absolute; right: 0; bottom: 0;
    width: 292px; height: 29px;
  }
  .tagline-band svg { position: absolute; inset: 0; }
  .tagline-text {
    position: absolute; right: 16px; top: 7px;
    color: var(--white); font-size: 12px;
    white-space: nowrap;
  }
</style>
</head>
<body>

<section class="card card--front">
  <div class="front-brand">
    <span class="brand-square"></span>
    <span class="brand-name">BuildMark Solutions</span>
  </div>
  <div class="services-band">
    <p>New Software Implementations<span class="sep">|</span>Software Re-Implementations</p>
    <p>Redesigning Software Usage at the User Level</p>
    <p>Project Coordination &amp; Management<span class="sep">|</span>Continued Software Support</p>
  </div>
  <div class="front-web">
    <span class="rule"></span>
    <span>www.buildmark-solutions.example</span>
    <span class="rule"></span>
  </div>
</section>

<section class="card card--back">
  <div class="back-brand">BuildMark Solutions</div>
  <span class="name-marker"></span>
  <h1 class="person-name">Dana R. Whitfield</h1>
  <p class="person-role">Owner</p>
  <ul class="contact-list">
    <li>
      <svg viewBox="0 0 12 12" aria-hidden="true"><path d="M3 0h6a1 1 0 0 1 1 1v10a1 1 0 0 1-1 1H3a1 1 0 0 1-1-1V1a1 1 0 0 1 1-1zm.5 1.5v8h5v-8z"/></svg>
      <span>555-013-4820</span>
    </li>
    <li>
      <svg viewBox="0 0 12 12" aria-hidden="true"><path d="M0 4c0-2 3-3 6-3s6 1 6 3v1H9V3.5H3V5H0zM2 6h8l1 5H1z"/></svg>
      <span>555-017-2394 ext. 12</span>
    </li>
    <li>
      <svg viewBox="0 0 12 12" aria-hidden="true"><path d="M0 2h12v8H0zm1 1.2V9h10V3.2L6 6.5z"/></svg>
      <span>dana.whitfield@buildmark-solutions.example</span>
    </li>
    <li>
      <svg viewBox="0 0 12 12" aria-hidden="true"><path d="M6 0a6 6 0 1 0 0 12A6 6 0 0 0 6 0zm0 1c.8 0 1.6 1.6 1.9 4H4.1C4.4 2.6 5.2 1 6 1zM1 6h2.1c0 .4 0 .8.1 1.2H1.1A5 5 0 0 1 1 6zm3.1 1.2h3.8C7.6 9.5 6.8 11 6 11s-1.6-1.5-1.9-3.8zm4.7 0H11A5 5 0 0 1 11 6H8.9z"/></svg>
      <span>www.<span class="web-accent">buildmark-solutions</span>.example</span>
    </li>
  </ul>
  <address class="address">
    14B Harbor Street - PMB 118<br>
    Millbrook Falls, NY 10999
  </address>
  <div class="tagline-band">
    <svg viewBox="0 0 292 29" preserveAspectRatio="none" aria-hidden="true">
      <path d="M22 0H292V29H0z" fill="var(--brand-blue)"/>
    </svg>
    <span class="tagline-text">Mapping Choices - Building Better Systems</span>
  </div>
</section>

</body>
</html>
```